Business Card Design for Property Development Company Director

I am looking for a professional and unforgettable business card design for our Director of our Property Development Company.
Please see attached .pptx file to find out what information to include. You don't have to follow the exact format shown in the file - I am interested to see your creative flair using the information provided.

```html
<!DOCTYPE html>
<html lang="en">
<head>
<meta charset="UTF-8">
<title>Norvale Property Group – Business Card</title>
<link href="https://fonts.googleapis.com/css2?family=Montserrat:wght@400;500;700&display=swap" rel="stylesheet">
<style>
  :root {
    --canvas: #f2f2f2;
    --card-white: #ffffff;
    --brand-blue: #1656a3;
    --text-grey: #555a60;
    --on-blue: #ffffff;
  }
  * { margin: 0; padding: 0; box-sizing: border-box; }
  html, body { width: 1200px; height: 800px; overflow: hidden; }
  body {
    background: var(--canvas);
    font-family: "Montserrat", sans-serif;
    display: flex;
    align-items: center;
    justify-content: center;
    gap: 48px;
  }
  .card {
    width: 520px;
    height: 318px;
    position: relative;
    box-shadow: 0 6px 18px rgba(0,0,0,0.12);
  }
  .card--front { background: var(--card-white); color: var(--text-grey); }
  .card--back { background: var(--brand-blue); color: var(--on-blue); }

  .brand { display: flex; align-items: center; gap: 10px; }
  .brand__mark { width: 26px; height: 26px; flex: none; }
  .brand__name {
    font-weight: 700;
    font-size: 22px;
    letter-spacing: 1px;
    line-height: 1.05;
    text-transform: uppercase;
  }
  .card--front .brand { position: absolute; top: 30px; left: 34px; }
  .card--front .brand__mark { background: var(--brand-blue); }
  .card--front .brand__name { color: var(--brand-blue); }

  .contact { position: absolute; left: 236px; top: 100px; font-size: 12.5px; line-height: 1.5; }
  .contact__name { color: var(--brand-blue); font-weight: 500; font-size: 19px; letter-spacing: 0.3px; }
  .contact__role { margin-bottom: 6px; }
  .contact__address { margin-bottom: 6px; }
  .contact__line { display: flex; align-items: center; gap: 7px; }
  .contact__line svg { width: 10px; height: 10px; fill: var(--brand-blue); flex: none; }

  .licence { position: absolute; left: 34px; bottom: 22px; font-size: 12.5px; white-space: nowrap; }
  .licence__label { color: var(--brand-blue); font-weight: 500; }

  .tagline {
    position: absolute; top: 34px; right: 36px;
    text-align: right; font-size: 13px; line-height: 1.45;
  }
  .card--back .brand { position: absolute; top: 126px; right: 60px; }
  .card--back .brand__mark { background: var(--on-blue); }
  .card--back .brand__name { font-size: 28px; }
  .invite { position: absolute; left: 36px; bottom: 28px; font-size: 12.5px; font-weight: 500; }
</style>
</head>
<body>
  <section class="card card--front">
    <div class="brand">
      <span class="brand__mark"></span>
      <span class="brand__name">Norvale<br>Property Group</span>
    </div>
    <div class="contact">
      <p class="contact__name">DANIEL MARSH</p>
      <p class="contact__role">Director</p>
      <p class="contact__address">57 Carrow St.<br>Brunswick VIC 3056, Australia</p>
      <p class="contact__line"><svg viewBox="0 0 10 10"><path d="M2 0h2l1 2.5-1.3 1a6 6 0 0 0 2.8 2.8l1-1.3L10 6v2a2 2 0 0 1-2 2A8 8 0 0 1 0 2a2 2 0 0 1 2-2z"/></svg>0400 218 635</p>
      <p class="contact__line"><svg viewBox="0 0 10 10"><path d="M0 2h10v6H0zM0 2l5 3.5L10 2" stroke="#fff" stroke-width="0.8"/></svg>daniel@norvale.com.au</p>
      <p class="contact__line"><svg viewBox="0 0 10 10"><circle cx="5" cy="5" r="5"/></svg>www.norvale.com.au</p>
    </div>
    <p class="licence"><span class="licence__label">Real Estate Lic:</span> 5120394 &amp; 5120395</p>
  </section>

  <section class="card card--back">
    <p class="tagline">Property Development<br>&amp; Site Acquisition Specialists</p>
    <div class="brand">
      <span class="brand__mark"></span>
      <span class="brand__name">Norvale<br>Property Group</span>
    </div>
    <p class="invite">Ask me about our INVESTMENT &amp; PARTNERSHIP opportunities</p>
  </section>
</body>
</html>
```